We need a website for an ice cream shop "plover ice cream"

We are opening an ice cream shop called "plover ice cream". We already have a logo (photo attached). The ice cream shop will be in the style of "Harbor Static" movie - palm trees, sunset, there will be a flamingo on the wall, so basically sunset, beach, Miami style. We would like the website to be colorful, colors of sunset, colorful buildings, girls wearing vintage roller skates. You can get inspiration from the "Harbor Static" movie. We would like the website to be playful, a little vintage, not boring. The website should attract people's attention.

Target Market(s)

everyone

Industry/Entity Type

ice cream shop

Number of Pages Required

5+ page

Font styles to use
Sans Serif
Script

Colors
0094D4
00A9DD
6FCCEA
C7EBF8
E9F6FB
FFC000
F8CF3A
FAE287
FDF2CF
FEFAEE
F0912C
F2A743
F7CA91
FBE8D2
FDF5EE
EE7325
F08F49
F5BC92
FAE3D3
FDF4ED
E54698
E96AAD
F1A4CE
F9D9EA
FCEFF6
A7469A
B969AE
D3A5CF
EDDBEB
F8F0F9

Requirements
Must have
• tropical, Miami style, sunset
Nice to have
• palm trees, flamingo, girls on vintage roller skates, sea, colorful buildings

```html
<!DOCTYPE html>
<html lang="en">
<head>
<meta charset="utf-8">
<title>Plover Ice Cream</title>
<link rel="stylesheet" href="https://fonts.googleapis.com/css2?family=Allura&family=Barlow:wght@400;500;600;700&family=Bebas+Neue&family=Lexend:wght@500;600;700&family=Oswald:wght@400;500&display=swap">
<style>
:root{
  --navy:#1c2463;
  --ink:#2b2b3a;
  --text:#4a4a55;
  --pink:#e54698;
  --pink-soft:#e96aad;
  --pink-pale:#f9d9ea;
  --blue:#0094d4;
  --blue-mid:#00a9dd;
  --sky:#6fccea;
  --sky-pale:#c7ebf8;
  --violet:#a7469a;
  --lilac:#d3a5cf;
  --white:#ffffff;
  --footer-ink:#2c3b7a;
}
*{margin:0;padding:0;box-sizing:border-box}
html,body{width:1200px;height:3881px;overflow:hidden}
body{position:relative;background:var(--white);font-family:"Barlow",sans-serif;color:var(--text)}
.abs{position:absolute}
.script{font-family:"Allura",cursive;color:var(--pink);font-weight:400}
.btn{position:absolute;display:flex;align-items:center;justify-content:space-between;padding:0 6px 0 28px;border-radius:30px;background:linear-gradient(90deg,var(--pink),var(--violet) 55%,var(--blue-mid));color:var(--white);font-family:"Oswald",sans-serif;font-size:18px;letter-spacing:.3px;text-decoration:none}
.btn .arrow{width:34px;height:34px;border-radius:50%;background:var(--blue-mid);display:flex;align-items:center;justify-content:center}
.ph{position:absolute}

/* header */
.site-header{position:absolute;left:0;top:0;width:1200px;height:100px;background:var(--white);z-index:3}
.brand{position:absolute;left:112px;top:32px;display:flex;align-items:center;gap:8px}
.brand-dot{width:38px;height:38px;border-radius:50%;background:var(--navy);flex:none}
.brand-name{font-family:"Lexend",sans-serif;font-weight:700;font-size:16px;color:var(--navy);line-height:1;white-space:nowrap}
.nav{position:absolute;top:42px;left:0;width:100%;font-family:"Oswald",sans-serif;font-size:18px;color:var(--navy)}
.nav a{position:absolute;color:inherit;text-decoration:none}
.nav .active{color:var(--blue-mid)}
.nav .active::after{content:"";position:absolute;left:0;right:0;bottom:-8px;height:2px;background:var(--pink)}
.call{position:absolute;left:927px;top:35px;width:170px;height:40px;border-radius:20px;background:linear-gradient(90deg,var(--pink),var(--blue-mid));color:var(--white);font-family:"Oswald",sans-serif;font-size:16px;display:flex;align-items:center;gap:8px;padding-left:20px}

/* hero */
.hero{position:absolute;left:0;top:100px;width:1200px;height:660px;background:linear-gradient(180deg,#8fd6ea 0%,#c9e3f3 35%,#efc9ec 75%,#f4c9ef 100%)}
.hero-script{position:absolute;left:0;width:700px;top:150px;text-align:center;font-size:54px}
.hero-title{position:absolute;left:0;width:700px;top:205px;text-align:center;font-family:"Bebas Neue",sans-serif;font-weight:400;font-size:60px;color:var(--navy);letter-spacing:.5px}
.hero-mascot{left:125px;top:350px;width:450px;height:250px;border-radius:45%;background:radial-gradient(ellipse at 50% 50%,#4a86c4 0%,#7fb2de 45%,rgba(239,201,236,0) 72%)}
.hero-photo{left:650px;top:70px;width:490px;height:490px;border-radius:50%;border:6px solid var(--white);background:linear-gradient(160deg,#6c7fe0,#b38ae0 50%,#f3b6cf)}

/* about */
.about{position:absolute;left:0;top:745px;width:1200px;height:708px;background:linear-gradient(180deg,#ffffff 0%,#f7eef8 50%,#eef6fb 100%)}
.about-ring{left:90px;top:80px;width:500px;height:500px;border-radius:50%;background:conic-gradient(from 200deg,var(--sky),var(--pink) 40%,var(--pink) 60%,var(--sky))}
.about-photo{left:102px;top:92px;width:476px;height:476px;border-radius:50%;border:6px solid var(--white);background:linear-gradient(160deg,#7db36b,#c9b08e 55%,#e58a8a)}
.about-script{left:630px;top:130px;font-size:60px}
.about-title{left:635px;top:198px;font-family:"Lexend",sans-serif;font-weight:600;font-size:34px;color:var(--navy);letter-spacing:.5px}
.about-copy{left:636px;top:262px;width:470px;font-size:16px;line-height:25.6px;text-align:justify;color:var(--text)}

/* menu */
.menu{position:absolute;left:0;top:1453px;width:1200px;height:630px;background:linear-gradient(180deg,#d8f2fb 0%,#86dbe0 30%,#a8e2e4 55%,#f3cfe8 80%,#f7d8ee 100%)}
.section-script{position:absolute;left:0;width:1200px;text-align:center;font-size:44px}
.section-title{position:absolute;left:0;width:1200px;text-align:center;font-family:"Lexend",sans-serif;font-weight:700;color:var(--navy)}
.menu-card{position:absolute;top:345px;width:214px;height:214px;border-radius:50%;background:var(--white);text-align:center;padding-top:100px;box-shadow:0 8px 0 var(--ring)}
.menu-card h3{font-family:"Lexend",sans-serif;font-weight:600;font-size:20px;color:var(--navy)}
.menu-card p{font-size:14px;color:var(--text);margin-top:2px}
.menu-card strong{display:block;font-size:17px;font-weight:700;color:var(--ink);margin-top:8px}
.cone-photo{position:absolute;top:130px;width:130px;height:300px;border-radius:65px 65px 40px 40px;opacity:.92}
.chev{position:absolute;top:325px}

/* gallery */
.gallery{position:absolute;left:0;top:2065px;width:1200px;height:780px;background:linear-gradient(160deg,#0aa4e6 0%,#2aa5e8 30%,#b08add 65%,#f070c0 100%)}
.gallery .section-script,.gallery .section-title{color:var(--white)}
.tile{position:absolute;border-radius:2px}

/* contact */
.contact-script{left:138px;top:2982px;font-size:56px}
.contact-title{left:138px;top:3038px;font-family:"Lexend",sans-serif;font-weight:600;font-size:38px;color:#3a3a46}
.contact-copy{left:140px;top:3092px;width:360px;font-size:14px;line-height:22px}
.ci{position:absolute;left:137px;width:48px;height:48px;border-radius:50%;background:linear-gradient(135deg,var(--pink),var(--violet) 50%,var(--blue-mid));display:flex;align-items:center;justify-content:center}
.ci-label{position:absolute;left:200px;font-size:15px;color:#555}
.ci-value{position:absolute;left:200px;font-size:22px;color:#333}
.form-panel{left:611px;top:2960px;width:476px;height:420px;background:linear-gradient(140deg,#1c1747,#2b1d61 60%,#1b1643);border-radius:30px 60px 0 30px}
.flamingo-glow{left:180px;top:80px;width:180px;height:280px;border-radius:45%;background:radial-gradient(ellipse,rgba(233,106,173,.45),rgba(233,106,173,0) 70%)}
.field{position:absolute;left:41px;width:398px;height:44px;border:1.5px solid #b9b6d6;display:flex;align-items:center;gap:10px;padding-left:16px;color:#e8e6f5;font-size:13px}
.submit{position:absolute;left:41px;top:343px;width:137px;height:40px;border-radius:20px;background:var(--pink-soft);color:var(--white);font-family:"Lexend",sans-serif;font-weight:600;font-size:17px;display:flex;align-items:center;justify-content:center}

/* footer */
.site-footer{position:absolute;left:0;top:3455px;width:1200px;height:426px;background:linear-gradient(180deg,#a9dff0 0%,#cfe6f3 50%,#e8e3f4 100%)}
.footer-brand{left:130px;top:140px;display:flex;align-items:center;gap:10px}
.footer-col h4{position:absolute;font-family:"Lexend",sans-serif;font-weight:600;font-size:18px;color:var(--footer-ink)}
.qlinks{left:400px;top:130px;list-style:none;font-size:13px;color:var(--footer-ink);line-height:26px}
.ficon{position:absolute;width:32px;height:32px;border-radius:50%;background:var(--blue-mid);display:flex;align-items:center;justify-content:center}
.ftext{position:absolute;font-size:12.5px;line-height:19px;color:var(--footer-ink)}
.ftext b{font-weight:700}
.social{position:absolute;top:183px;width:28px;height:28px;border-radius:50%}
.footer-rule{left:0;top:340px;width:1200px;height:1px;background:#9fb3cf}
.copyright{left:0;top:355px;width:1200px;text-align:center;font-size:12px;color:var(--footer-ink)}
</style>
</head>
<body>

<header class="site-header">
  <div class="brand"><span class="brand-dot"></span><span class="brand-name">plover ice cream</span></div>
  <nav class="nav">
    <a class="active" style="left:340px">HOME</a>
    <a style="left:443px">ABOUT US</a>
    <a style="left:576px">PHOTOS</a>
    <a style="left:698px">MENUS</a>
    <a style="left:810px">CONTACT</a>
  </nav>
  <div class="call">
    <svg width="16" height="16" viewBox="0 0 24 24"><path fill="#fff" d="M6.6 10.8a15.1 15.1 0 006.6 6.6l2.2-2.2c.3-.3.7-.4 1-.2 1.1.4 2.3.6 3.6.6.6 0 1 .4 1 1V20c0 .6-.4 1-1 1A17 17 0 013 4c0-.6.4-1 1-1h3.5c.6 0 1 .4 1 1 0 1.3.2 2.5.6 3.6.1.3 0 .7-.2 1z"/></svg>
    (123) 456 7890
  </div>
</header>

<section class="hero">
  <div class="hero-script script">Plover Ice creame</div>
  <h1 class="hero-title">ENJOY YOUR EVERY BITE</h1>
  <a class="btn" style="left:267px;top:288px;width:156px;height:46px">VIEW MENU <span class="arrow"><svg width="18" height="18" viewBox="0 0 24 24"><path d="M4 12h15M13 6l6 6-6 6" stroke="#fff" stroke-width="2.4" fill="none"/></svg></span></a>
  <div class="ph hero-mascot" role="img" aria-label="Cartoon mascot holding two ice cream cones"></div>
  <div class="ph hero-photo" role="img" aria-label="Smiling man holding a vanilla cone against a palm tree sunset"></div>
  <svg class="abs" style="left:0;bottom:-2px" width="1200" height="30" viewBox="0 0 1200 30"><path fill="#fff" d="M0 10 L40 14 L80 8 L130 15 L180 9 L240 16 L300 10 L360 15 L420 8 L480 14 L540 9 L600 16 L660 10 L720 14 L780 8 L840 15 L900 10 L960 16 L1020 9 L1080 14 L1140 8 L1200 13 L1200 30 L0 30Z"/></svg>
</section>

<section class="about">
  <div class="ph about-ring"></div>
  <div class="ph about-photo" role="img" aria-label="Family of three enjoying ice cream cones in a park"></div>
  <div class="abs about-script script">About Us</div>
  <h2 class="abs about-title">PLOVER ICE CREAME</h2>
  <p class="abs about-copy">Lorem Ipsum is simply dummy text of the printing and typesetting industry. Lorem Ipsum has been the industry's standard dummy text ever since the 1500s, when an unknown printer took a galley of type and scrambled it to make a type specimen book. It has survived not only five centuries, but also the leap into electronic typesetting, remaining essentially unchanged.</p>
  <a class="btn" style="left:627px;top:445px;width:157px;height:46px">READ MORE <span class="arrow"><svg width="18" height="18" viewBox="0 0 24 24"><path d="M4 12h15M13 6l6 6-6 6" stroke="#fff" stroke-width="2.4" fill="none"/></svg></span></a>
</section>

<section class="menu">
  <div class="section-script script" style="top:25px">Order now</div>
  <h2 class="section-title" style="top:68px;font-size:42px">OUR MENU</h2>
  <svg class="chev" style="left:80px" width="26" height="40" viewBox="0 0 26 40"><path d="M20 4 L6 20 L20 36" stroke="var(--navy)" stroke-width="4" fill="none"/></svg>
  <svg class="chev" style="left:1104px" width="26" height="40" viewBox="0 0 26 40"><path d="M6 4 L20 20 L6 36" stroke="var(--navy)" stroke-width="4" fill="none"/></svg>

  <div class="menu-card" style="left:153px;--ring:var(--pink-soft)"><h3>ICE CREAME</h3><p>Vanilla Flavour</p><strong>$25.99</strong></div>
  <div class="menu-card" style="left:383px;--ring:#fae287"><h3>ICE CREAME</h3><p>Vanilla Flavour</p><strong>$25.99</strong></div>
  <div class="menu-card" style="left:615px;--ring:var(--lilac)"><h3>ICE CREAME</h3><p>Vanilla Flavour</p><strong>$25.99</strong></div>
  <div class="menu-card" style="left:849px;--ring:#f2a743"><h3>ICE CREAME</h3><p>Vanilla Flavour</p><strong>$25.99</strong></div>

  <div class="cone-photo" style="left:195px;background:linear-gradient(180deg,#f1a4ce,#ecb3c8 45%,#e3b77a)" role="img" aria-label="Strawberry soft serve cone"></div>
  <div class="cone-photo" style="left:425px;background:linear-gradient(180deg,#f6f0df,#efe2c3 45%,#e3b77a)" role="img" aria-label="Vanilla soft serve cone"></div>
  <div class="cone-photo" style="left:657px;background:linear-gradient(180deg,#c0a8ec,#a98ae0 50%,#8f68cc)" role="img" aria-label="Blueberry soft serve cone"></div>
  <div class="cone-photo" style="left:891px;background:linear-gradient(180deg,#9a6a52,#b88a62 45%,#e3b77a)" role="img" aria-label="Chocolate soft serve cone"></div>
</section>

<section class="gallery">
  <svg class="abs" style="left:0;top:-2px" width="1200" height="30" viewBox="0 0 1200 30"><path fill="#f7d8ee" d="M0 0 H1200 V12 L1140 18 L1080 10 L1020 17 L960 11 L900 18 L840 10 L780 16 L720 9 L660 17 L600 11 L540 18 L480 10 L420 16 L360 9 L300 17 L240 11 L180 18 L120 10 L60 16 L0 12Z"/></svg>
  <div class="section-script script" style="top:60px;color:#fff">Our gallery</div>
  <h2 class="section-title" style="top:100px;font-size:38px">PHOTO GALLERY</h2>
  <div class="tile" style="left:102px;top:176px;width:242px;height:205px;background:linear-gradient(160deg,#d7c3b0,#f1e5dc 60%,#9fc4d8)" role="img" aria-label="Server smiling behind an ice cream counter"></div>
  <div class="tile" style="left:102px;top:397px;width:242px;height:206px;background:linear-gradient(160deg,#6e4a3a,#e4b56a 55%,#c49075)" role="img" aria-label="Two hands holding ice cream cones"></div>
  <div class="tile" style="left:356px;top:176px;width:242px;height:427px;background:linear-gradient(180deg,#cfcac6,#e2b49b 40%,#f1c66b 75%,#8a8a8c)" role="img" aria-label="Woman holding two ice cream cones"></div>
  <div class="tile" style="left:611px;top:176px;width:242px;height:205px;background:linear-gradient(160deg,#c8a88c,#f2ede8 50%,#b35a6a)" role="img" aria-label="Plated ice cream desserts on a table"></div>
  <div class="tile" style="left:611px;top:397px;width:242px;height:206px;background:linear-gradient(160deg,#c98d6a,#e5d3c3 50%,#7a6a6a)" role="img" aria-label="Woman dancing in an ice cream parlour"></div>
  <div class="tile" style="left:862px;top:176px;width:243px;height:427px;background:linear-gradient(180deg,#c9c7c5,#f3e7b7 40%,#e2475a 70%,#f0ce8a)" role="img" aria-label="Display case of gelato flavours"></div>
  <a class="btn" style="left:528px;top:637px;width:158px;height:46px">VIEWMORE <span class="arrow"><svg width="18" height="18" viewBox="0 0 24 24"><path d="M4 12h15M13 6l6 6-6 6" stroke="#fff" stroke-width="2.4" fill="none"/></svg></span></a>
  <svg class="abs" style="left:0;bottom:-2px" width="1200" height="30" viewBox="0 0 1200 30"><path fill="#fff" d="M0 14 L60 8 L120 16 L180 10 L240 17 L300 9 L360 15 L420 10 L480 17 L540 9 L600 15 L660 8 L720 16 L780 10 L840 17 L900 9 L960 15 L1020 10 L1080 16 L1140 9 L1200 14 L1200 30 L0 30Z"/></svg>
</section>

<section class="contact">
  <div class="abs contact-script script">Our Shop</div>
  <h2 class="abs contact-title">CONTACT US</h2>
  <p class="abs contact-copy">Lorem Ipsum is simply dummy text of the printing and typesetting industry Lorem Ipsum is simply dummy</p>
  <span class="ci" style="top:3186px"><svg width="22" height="22" viewBox="0 0 24 24"><path fill="#fff" d="M6.6 10.8a15.1 15.1 0 006.6 6.6l2.2-2.2c.3-.3.7-.4 1-.2 1.1.4 2.3.6 3.6.6.6 0 1 .4 1 1V20c0 .6-.4 1-1 1A17 17 0 013 4c0-.6.4-1 1-1h3.5c.6 0 1 .4 1 1 0 1.3.2 2.5.6 3.6.1.3 0 .7-.2 1z"/></svg></span>
  <div class="ci-label" style="top:3170px">PHONE NUMBER</div>
  <div class="ci-value" style="top:3192px;font-weight:700">+47 900 12 345</div>
  <span class="ci" style="top:3262px"><svg width="22" height="22" viewBox="0 0 24 24"><rect x="3" y="6" width="18" height="13" rx="1" fill="none" stroke="#fff" stroke-width="2"/><path d="M3 7l9 7 9-7" fill="none" stroke="#fff" stroke-width="2"/></svg></span>
  <div class="ci-label" style="top:3245px">EMAIL US</div>
  <div class="ci-value" style="top:3268px">info@plover ice cream</div>

  <div class="ph form-panel">
    <div class="ph flamingo-glow" role="img" aria-label="Pink neon flamingo sign on a brick wall"></div>
    <div class="field" style="top:42px"><svg width="13" height="13" viewBox="0 0 24 24"><circle cx="12" cy="8" r="5" fill="#fff"/><path d="M3 22c0-5 4-8 9-8s9 3 9 8z" fill="#fff"/></svg>First name</div>
    <div class="field" style="top:95px"><svg width="13" height="13" viewBox="0 0 24 24"><circle cx="12" cy="8" r="5" fill="#fff"/><path d="M3 22c0-5 4-8 9-8s9 3 9 8z" fill="#fff"/></svg>Last name</div>
    <div class="field" style="top:148px"><svg width="13" height="13" viewBox="0 0 24 24"><path fill="#fff" d="M6.6 10.8a15.1 15.1 0 006.6 6.6l2.2-2.2c.3-.3.7-.4 1-.2 1.1.4 2.3.6 3.6.6.6 0 1 .4 1 1V20c0 .6-.4 1-1 1A17 17 0 013 4c0-.6.4-1 1-1h3.5c.6 0 1 .4 1 1 0 1.3.2 2.5.6 3.6.1.3 0 .7-.2 1z"/></svg>Phone number</div>
    <div class="field" style="top:201px"><svg width="13" height="13" viewBox="0 0 24 24"><rect x="2" y="5" width="20" height="14" fill="#fff"/><path d="M2 6l10 7 10-7" fill="none" stroke="#2b1d61" stroke-width="2"/></svg>Email address</div>
    <div class="field" style="top:252px;height:80px;align-items:flex-start;padding-top:8px">Comments</div>
    <div class="submit">SUBMIT</div>
  </div>
</section>

<footer class="site-footer">
  <div class="abs footer-brand"><span class="brand-dot" style="width:56px;height:56px"></span><span class="brand-name" style="font-size:20px">plover ice cream</span></div>
  <div class="footer-col">
    <h4 style="left:400px;top:82px">QUICK LINKS</h4>
    <ul class="abs qlinks"><li>» About us</li><li>» Our Menu</li><li>» Gallery</li><li>» Contact Us</li></ul>

    <h4 style="left:605px;top:82px">OUR SHOP</h4>
    <span class="ficon" style="left:607px;top:121px"><svg width="16" height="16" viewBox="0 0 24 24"><path fill="#fff" d="M12 2a7 7 0 00-7 7c0 5 7 13 7 13s7-8 7-13a7 7 0 00-7-7zm0 9.5A2.5 2.5 0 1112 6a2.5 2.5 0 010 5.5z"/></svg></span>
    <div class="ftext" style="left:648px;top:120px">123 Lorem Ipsum Address line<br>tempor incididunt ut la</div>
    <span class="ficon" style="left:607px;top:172px"><svg width="16" height="16" viewBox="0 0 24 24"><path fill="#fff" d="M6.6 10.8a15.1 15.1 0 006.6 6.6l2.2-2.2c.3-.3.7-.4 1-.2 1.1.4 2.3.6 3.6.6.6 0 1 .4 1 1V20c0 .6-.4 1-1 1A17 17 0 013 4c0-.6.4-1 1-1h3.5c.6 0 1 .4 1 1 0 1.3.2 2.5.6 3.6.1.3 0 .7-.2 1z"/></svg></span>
    <div class="ftext" style="left:648px;top:171px">Phone Number<br><b>(123) 456 7890</b></div>

    <h4 style="left:860px;top:82px">GET IN TOUCH</h4>
    <span class="ficon" style="left:862px;top:119px"><svg width="16" height="16" viewBox="0 0 24 24"><rect x="3" y="6" width="18" height="13" rx="1" fill="none" stroke="#fff" stroke-width="2"/><path d="M3 7l9 7 9-7" fill="none" stroke="#fff" stroke-width="2"/></svg></span>
    <div class="ftext" style="left:905px;top:118px">Email address<br><b>order@plovericecream.com</b></div>
    <span class="social" style="left:869px;background:var(--pink-soft)"></span>
    <span class="social" style="left:906px;background:var(--pink-soft)"></span>
    <span class="social" style="left:943px;background:var(--pink-soft)"></span>
    <span class="social" style="left:981px;background:var(--pink-soft)"></span>
  </div>
  <div class="abs footer-rule"></div>
  <div class="abs copyright">Copyright © 2022 Plover Ice Creame | All Rights Reserved</div>
</footer>

</body>
</html>
```